Interior design service, along with home organization, packing, and staging, home and business. As well as staging in conjunction with real estate sales.
Updates

Love many of your designs and will be choosing today. To inform you of the exact details needed, the name of the company is "Flourish by Marnie T" , my phone number and e-,ail need to be included. i also need either description or some sort of bullet points that give an idea of the following:

- Interior design for home and business
- Home organization and packing
- Staging for personal and professional space
- Real estate stagingĀ 

Thank you

Target Market(s)

wide audience, but most importantly people looking for a quality service

Industry/Entity Type

Real Estate

Contact Information for Business Card

Flourish By Marnie T
Marnie Tolvery
(555)687-3914
mtbrisco@postwell.example

Requirements
Must have
• I'm 29 so i want my card to reflect something professional but still fresh. I don't have any specific photos or quotes that Ive included, however I like the card to reflect a personal touch, which is what I'm seeking from this service in the design of my card. Thanks!

```html
<!DOCTYPE html>
<html lang="en">
<head>
<meta charset="utf-8">
<title>Flourish By Marnie T – Business Card</title>
<link rel="stylesheet" href="https://fonts.googleapis.com/css2?family=Alegreya+Sans:wght@400;500;700&family=Tinos:wght@700&display=swap">
<style>
  :root {
    --stage: #4b4b4b;
    --paper: #f1f1f1;
    --paper-grey: #d9d9d9;
    --orange: #e07a12;
    --orange-light: #f6a623;
    --gold: #ffd34a;
    --brown: #6b3a12;
    --brown-dark: #2e1a0c;
    --panel: rgba(40, 38, 36, 0.84);
    --white: #ffffff;
    --bleed: #e0222c;
    --safe: #22b4e6;
  }
  html, body {
    margin: 0;
    width: 1200px;
    height: 960px;
    overflow: hidden;
    background: var(--stage);
  }
  .canvas {
    position: relative;
    width: 1200px;
    height: 960px;
  }
  .card {
    position: absolute;
    display: block;
  }
  .card--front { left: 120px; top: 58px; }
  .card--back  { left: 534px; top: 442px; }

  .headline {
    font-family: "Alegreya Sans", "Segoe UI", sans-serif;
    font-weight: 500;
    fill: var(--white);
  }
  .headline--lg { font-size: 46px; }
  .headline--md { font-size: 35px; }

  .serif { font-family: "Tinos", "Times New Roman", serif; font-weight: 700; fill: var(--white); }
  .business-label { font-size: 12px; }
  .owner-name { font-size: 24px; }
  .contact-label { font-size: 23px; }
  .contact-value { font-size: 15px; letter-spacing: 0.3px; }

  .service-list {
    font-family: "Alegreya Sans", "Segoe UI", sans-serif;
    font-weight: 500;
    font-size: 13px;
    fill: var(--white);
  }
  .service-bullet { fill: var(--orange-light); }

  .guide-bleed { fill: none; stroke: var(--bleed); stroke-width: 1; }
  .guide-safe  { fill: none; stroke: var(--safe); stroke-width: 1; }
</style>
</head>
<body>
<main class="canvas">

  <!-- Front side -->
  <svg class="card card--front" width="574" height="332" viewBox="0 0 574 332" aria-label="Business card front">
    <defs>
      <linearGradient id="front-paper" x1="0" y1="0" x2="1" y2="1">
        <stop offset="0" stop-color="var(--paper)"/>
        <stop offset="1" stop-color="var(--paper-grey)"/>
      </linearGradient>
      <linearGradient id="front-band" x1="0" y1="0" x2="1" y2="0">
        <stop offset="0" stop-color="var(--brown)"/>
        <stop offset="0.35" stop-color="var(--orange)"/>
        <stop offset="1" stop-color="var(--orange-light)"/>
      </linearGradient>
      <linearGradient id="front-arc" x1="0" y1="0" x2="1" y2="1">
        <stop offset="0" stop-color="var(--gold)"/>
        <stop offset="0.4" stop-color="var(--orange)"/>
        <stop offset="1" stop-color="var(--brown-dark)"/>
      </linearGradient>
      <radialGradient id="emblem-fill" cx="0.5" cy="0.5" r="0.5">
        <stop offset="0" stop-color="#fff6dc"/>
        <stop offset="0.45" stop-color="var(--gold)"/>
        <stop offset="0.75" stop-color="var(--orange)"/>
        <stop offset="1" stop-color="var(--brown)"/>
      </radialGradient>
    </defs>

    <rect class="card-base" width="574" height="332" fill="url(#front-paper)"/>

    <path class="corner-arc" d="M400 0 C470 30 524 80 574 150 L574 0 Z" fill="url(#front-arc)"/>
    <path class="corner-arc-dark" d="M455 0 C505 30 548 70 574 110 L574 0 Z" fill="var(--brown-dark)"/>

    <path class="lower-band" d="M0 332 L0 300 C120 260 300 240 574 262 L574 332 Z" fill="url(#front-band)"/>
    <path class="lower-band-dark" d="M0 332 L0 318 C150 288 340 276 574 292 L574 332 Z" fill="var(--brown)" opacity="0.55"/>

    <circle class="emblem" cx="182" cy="100" r="124" fill="url(#emblem-fill)" role="img" aria-label="Decorative round ornament in orange and gold"/>

    <rect class="headline-panel" x="184" y="116" width="390" height="165" fill="var(--panel)"/>
    <text class="headline headline--md" x="530" y="164" text-anchor="end">Are you</text>
    <text class="headline headline--md" x="530" y="208" text-anchor="end">looking for a</text>
    <text class="headline headline--lg" x="530" y="258" text-anchor="end">quality service?</text>

    <rect class="guide-bleed" x="9" y="9" width="556" height="314"/>
    <rect class="guide-safe" x="18" y="18" width="538" height="296"/>
  </svg>

  <!-- Back side -->
  <svg class="card card--back" width="572" height="330" viewBox="0 0 572 330" aria-label="Business card back">
    <defs>
      <linearGradient id="back-base" x1="0" y1="0" x2="1" y2="0">
        <stop offset="0" stop-color="#8a4a18"/>
        <stop offset="0.5" stop-color="#5a3418"/>
        <stop offset="1" stop-color="#3a2412"/>
      </linearGradient>
      <linearGradient id="back-glow" x1="0" y1="0" x2="1" y2="1">
        <stop offset="0" stop-color="var(--gold)"/>
        <stop offset="0.5" stop-color="var(--orange)"/>
        <stop offset="1" stop-color="var(--brown)"/>
      </linearGradient>
      <linearGradient id="back-light" x1="0" y1="0" x2="1" y2="1">
        <stop offset="0" stop-color="#ffffff"/>
        <stop offset="1" stop-color="#cfcfcf"/>
      </linearGradient>
    </defs>

    <rect class="card-base" width="572" height="330" fill="url(#back-base)"/>

    <polygon class="facet-light" points="0,170 150,60 230,330 0,330" fill="url(#back-light)" opacity="0.9"/>
    <polygon class="facet-light" points="200,0 270,0 140,330 90,330" fill="url(#back-light)" opacity="0.85"/>
    <polygon class="facet-orange" points="0,0 200,0 60,150 0,190" fill="url(#back-glow)"/>
    <polygon class="facet-dark" points="290,0 400,0 320,330 230,330" fill="#4a2a14" opacity="0.8"/>
    <path class="right-glow" d="M400 0 C470 60 450 200 530 330 L572 330 L572 0 Z" fill="url(#back-glow)" opacity="0.85"/>
    <path class="right-edge" d="M530 0 C566 80 548 200 572 260 L572 0 Z" fill="var(--brown-dark)"/>

    <!-- name panel -->
    <polygon class="name-panel" points="0,52 372,52 344,106 0,106" fill="var(--panel)"/>
    <text class="serif business-label" x="28" y="68">Flourish By Marnie T</text>
    <text class="serif owner-name" x="26" y="94">Marnie Tolvery</text>

    <!-- services panel -->
    <polygon class="services-panel" points="0,198 232,198 218,296 0,296" fill="var(--panel)"/>
    <g class="service-list">
      <circle class="service-bullet" cx="30" cy="217" r="2.5"/>
      <text x="38" y="221">Interior design, home &amp; business</text>
      <circle class="service-bullet" cx="30" cy="239" r="2.5"/>
      <text x="38" y="243">Home organization &amp; packing</text>
      <circle class="service-bullet" cx="30" cy="261" r="2.5"/>
      <text x="38" y="265">Personal &amp; professional staging</text>
      <circle class="service-bullet" cx="30" cy="283" r="2.5"/>
      <text x="38" y="287">Real estate staging</text>
    </g>

    <!-- contact panel -->
    <polygon class="contact-panel" points="294,168 572,168 572,278 244,278" fill="var(--panel)"/>
    <text class="serif contact-label" x="364" y="197" text-anchor="middle">Phone</text>
    <text class="serif contact-value" x="364" y="218" text-anchor="middle">(555)687-3914</text>
    <text class="serif contact-label" x="328" y="250" text-anchor="middle">Email</text>
    <text class="serif contact-value" x="392" y="270" text-anchor="middle">mtbrisco@postwell.example</text>

    <rect class="guide-bleed" x="9" y="9" width="554" height="312"/>
    <rect class="guide-safe" x="18" y="18" width="536" height="294"/>
  </svg>

</main>
</body>
</html>
```